Local Flower Farm Needs Business Card Design

I need business cards designed for a flower farm based in Eudora, Kansas.
Business Info:
We are a local cut flower farm located in Eudora, Kansas, founded by Corinne Haldwick. What started as a passion for agriculture and search for more joy in daily life has blossomed into a small business dedicated to providing the community with beautiful, fresh, and sustainable flowers. We specialize in local, seasonal blooms, ensuring that every petal reflects the care and dedication we pour into our craft. Our mission is to deliver the highest quality flowers directly to our customers through local farmers markets and to florists who share our commitment to sustainability. Join us in celebrating the beauty of nature, one bloom at a time!
Contact Details:
Corinne Haldwick
Owner
Phone 913-555-0147
Facebook: Rosalind Thorpe Gardens
Instagram: @RosalindThorpeGardens
Website: RosalindThorpeGardens.example
Target Market(s)
Wholesale to Florists and Direct to Consumer via Farmers Market
Industry/Entity Type
Florist, Farm
Contact Information for Business Card
Name, Contact Info, Logo
Look and feel
Each slider illustrates characteristics of the customer's brand and the style your logo design should communicate.

```html
<!DOCTYPE html>
<html lang="en">
<head>
<meta charset="utf-8">
<title>Rosalind Thorpe Gardens – Business Card</title>
<link href="https://fonts.googleapis.com/css2?family=Libre+Baskerville:wght@400;700&family=Poppins:ital,wght@0,400;1,300&display=swap" rel="stylesheet">
<style>
  :root {
    --backdrop: #e9e9e7;
    --paper: #f7f7f5;
    --ink: #0c2b2f;
    --teal-deep: #082225;
    --teal: #0d3538;
    --muted: #6d7476;
    --rule: #b9bdbd;
    --cream: #f1f1ee;
  }
  * { margin: 0; padding: 0; box-sizing: border-box; }
  html, body {
    width: 1200px; height: 1108px; overflow: hidden;
    background: var(--backdrop);
  }
  .sheet {
    width: 1200px; height: 1108px;
    display: flex; flex-direction: column; align-items: center;
    justify-content: center; gap: 108px;
  }
  .card {
    width: 700px; height: 400px; position: relative;
    box-shadow: 0 10px 30px rgba(0,0,0,0.18);
  }
  .card--front { background: var(--paper); color: var(--ink); }
  .card--back {
    background: radial-gradient(ellipse at 50% 40%, var(--teal) 0%, var(--teal-deep) 80%);
    display: flex; align-items: center; justify-content: center;
  }
  .brand-seal {
    position: absolute; left: 50px; top: 70px;
    width: 200px; height: 200px; border-radius: 50%;
    border: 1.5px solid var(--ink);
    display: flex; align-items: center; justify-content: center; text-align: center;
  }
  .brand-seal--large {
    position: static; width: 280px; height: 280px;
    border-color: var(--cream);
  }
  .brand-name {
    font-family: "Libre Baskerville", serif; font-weight: 400;
    font-size: 19px; line-height: 1.35; letter-spacing: 2px;
    text-transform: uppercase; color: var(--ink);
  }
  .brand-seal--large .brand-name { font-size: 26px; color: var(--cream); }
  .divider {
    position: absolute; left: 290px; top: 60px;
    width: 1px; height: 215px; background: var(--rule);
  }
  .person {
    position: absolute; left: 322px; top: 78px;
  }
  .person__name {
    font-family: "Libre Baskerville", serif; font-weight: 700;
    font-size: 32px; letter-spacing: 0.3px;
  }
  .person__role {
    font-family: "Poppins", sans-serif; font-style: italic; font-weight: 300;
    font-size: 14px; color: var(--muted); margin-top: -2px;
  }
  .contact {
    position: absolute; left: 322px; top: 172px;
    list-style: none;
    font-family: "Poppins", sans-serif; font-size: 15px; line-height: 26px;
  }
  .contact li { display: flex; align-items: center; gap: 12px; }
  .contact svg { width: 13px; height: 13px; flex: none; fill: var(--ink); }
  .social {
    position: absolute; left: 200px; top: 318px;
    display: flex; align-items: center; gap: 12px;
    font-family: "Poppins", sans-serif; font-size: 16px;
  }
  .social__dot {
    width: 20px; height: 20px; border-radius: 50%; background: var(--ink);
  }
</style>
</head>
<body>
<main class="sheet">
  <section class="card card--front" aria-label="Business card front">
    <div class="brand-seal">
      <span class="brand-name">Rosalind<br>Thorpe<br>Gardens</span>
    </div>
    <div class="divider"></div>
    <div class="person">
      <h1 class="person__name">Corinne Haldwick</h1>
      <p class="person__role">Owner</p>
    </div>
    <ul class="contact">
      <li>
        <svg viewBox="0 0 24 24" aria-hidden="true"><path d="M6.6 10.8a15.5 15.5 0 0 0 6.6 6.6l2.2-2.2c.3-.3.7-.4 1-.2 1.1.4 2.3.6 3.6.6.6 0 1 .4 1 1V20c0 .6-.4 1-1 1A17 17 0 0 1 3 4c0-.6.4-1 1-1h3.5c.6 0 1 .4 1 1 0 1.3.2 2.5.6 3.6.1.3 0 .7-.2 1z"/></svg>
        913-555-0147
      </li>
      <li>
        <svg viewBox="0 0 24 24" aria-hidden="true"><path d="M2 5h20v14H2zm2 2v.4l8 5.2 8-5.2V7zm0 2.8V17h16V9.8l-8 5.2z"/></svg>
        info@RosalindThorpeGardens.example
      </li>
      <li>
        <svg viewBox="0 0 24 24" aria-hidden="true"><circle cx="12" cy="12" r="10"/></svg>
        www.RosalindThorpeGardens.example
      </li>
    </ul>
    <div class="social">
      <span class="social__dot"></span>
      @RosalindThorpeGardens
    </div>
  </section>

  <section class="card card--back" aria-label="Business card back">
    <div class="brand-seal brand-seal--large">
      <span class="brand-name">Rosalind<br>Thorpe<br>Gardens</span>
    </div>
  </section>
</main>
</body>
</html>
```